Product Design for VelaMira

Design Brief for VelaMira Product Packaging

Objective:
Create a cohesive, elegant, and brand-consistent packaging design for the VelaMira product line. The signature visual theme should reflect luxury, femininity, and clean beauty values.

---

🎨 Core Design Direction

Unified Aesthetic: All containers must prominently feature the floral pattern shown in "Pattern Reference: Image 3". This design serves as the brand's signature aesthetic and must be applied uniformly across all SKUs.

Brand Logo Placement: The VelaMira logo (provided) should be clearly visible and harmoniously integrated into the patterned background.

Color Palette: Base colors should complement the brand’s primary palette: black, blush pink, and white.

---

🧴 Product-Specific Packaging Specifications

1. Mascara

Bottle Type: Sleek mascara tube with a wand applicator

Capacity: 5ml

Design: Use floral pattern from Pattern Reference Image 3. Ensure the pattern does not obstruct the readability of the logo or any regulatory text.

2. Eyebrow Growth Serum

Bottle Type: 5ml tube with fine-tip brush applicator

Capacity: 5ml

Design: Same floral pattern, scaled and applied proportionally to match the mascara for consistency

3. Eyelash Growth Serum

Bottle Type: 5ml tube with fine-tip brush (similar to the eyebrow serum, unless otherwise advised)

Capacity: 5ml

Design: Identical styling to maintain unity across lash & brow products

4. Anti-Aging Serum or Lotion

Bottle Type: 30ml airless pump bottle (preferred for hygiene and product stability)

Capacity: 30ml

Design: Apply floral pattern from Pattern Reference and scale appropriately for larger surface area

5. Hair Growth Spray

Bottle Type: 50ml fine mist spray bottle

Capacity: 50ml

Design: Pattern applied and scaled for taller profile; maintain visual harmony with skincare line

---

📦 Additional Notes

Please ensure packaging aligns with clean beauty standards (no overly glossy plastic finishes, avoid excessive secondary packaging unless sustainable).

Materials should be eco-conscious where possible.

If embossing, foil stamping, or UV finishing is available for logo accents, please suggest options.

```html
<!DOCTYPE html>
<html lang="en">
<head>
<meta charset="utf-8">
<title>VelaMira Packaging Line</title>
<link rel="stylesheet" href="https://fonts.googleapis.com/css2?family=Playfair+Display:wght@400&family=Catamaran:wght@400;500&display=swap">
<style>
  :root{
    --page:#f3f1f1;
    --blush-deep:#cf8a80;
    --blush-mid:#ddaaa2;
    --blush-light:#f4e6e4;
    --ink:#1a1414;
    --copy:#2b2222;
    --gold:#c9a24a;
    --flora:rgba(190,120,112,0.28);
  }
  *{box-sizing:border-box;margin:0;padding:0}
  html,body{width:1200px;height:1077px;overflow:hidden;background:var(--page)}
  .canvas{position:relative;width:1200px;height:1077px;background:var(--page)}

  .face{
    position:absolute;overflow:hidden;
    background:linear-gradient(160deg,var(--blush-deep) 0%,var(--blush-mid) 25%,var(--blush-light) 52%,var(--blush-mid) 75%,var(--blush-deep) 100%);
    box-shadow:0 2px 10px rgba(0,0,0,0.08);
  }
  .flora{
    position:absolute;border-radius:50%;
    background:radial-gradient(circle,var(--flora) 0%,rgba(190,120,112,0.12) 55%,rgba(190,120,112,0) 72%);
  }
  .flora--top{top:-6%;right:-18%;width:70%;height:45%}
  .flora--bottom{bottom:-8%;left:-20%;width:65%;height:38%}

  .logo{
    position:absolute;left:50%;
    font-family:"Playfair Display",serif;font-weight:400;color:var(--ink);
    white-space:nowrap;line-height:1;
  }
  .logo--vertical{writing-mode:vertical-rl;transform:translateX(-50%) rotate(180deg)}
  .logo--horizontal{transform:translateX(-50%)}

  .copy{
    position:absolute;left:0;right:0;text-align:center;
    font-family:"Catamaran",sans-serif;font-weight:400;color:var(--copy);line-height:1.15;
  }
  .rule{display:block;height:2px;margin:3px auto 4px;background:linear-gradient(90deg,rgba(201,162,74,0),var(--gold) 20%,var(--gold) 80%,rgba(201,162,74,0))}
  .volume{position:absolute;left:0;right:0;text-align:center;font-family:"Catamaran",sans-serif;color:var(--copy)}

  /* Hair growth box */
  .hair-box{left:66px;top:66px;width:176px;height:420px}
  .hair-box .logo{top:80px;font-size:40px}
  .hair-box .copy{top:292px;font-size:16px}
  .hair-box .rule{width:72px}
  .hair-box .volume{top:450px;top:auto;bottom:14px;font-size:16px}

  /* Hair growth bottle wrap */
  .hair-wrap{left:283px;top:155px;width:135px;height:330px}
  .hair-wrap .logo{top:42px;font-size:30px}
  .hair-wrap .copy{top:218px;font-size:13px}
  .hair-wrap .rule{width:58px}
  .hair-wrap .volume{bottom:12px;font-size:14px}

  /* Anti aging carton */
  .serum-box{left:569px;top:143px;width:335px;height:264px}
  .serum-box .logo{top:76px;font-size:30px}
  .serum-box .copy{top:144px;font-size:17px}
  .serum-box .rule{width:92px}
  .serum-box .volume{bottom:12px;font-size:14px}

  /* Anti aging dropper label */
  .serum-label{left:949px;top:271px;width:137px;height:173px}
  .serum-label .logo{top:52px;font-size:18px}
  .serum-label .copy{top:92px;font-size:11px}
  .serum-label .rule{width:58px}
  .serum-label .volume{bottom:6px;font-size:9px}

  /* Mascara */
  .mascara-box{left:71px;top:585px;width:149px;height:433px}
  .mascara-box .logo{top:110px;font-size:38px}
  .mascara-box .volume{bottom:28px;font-size:14px}
  .mascara-label{left:278px;top:743px;width:61px;height:275px}
  .mascara-label .logo{top:70px;font-size:17px}
  .mascara-label .volume{bottom:14px;font-size:8px}

  /* Eyelash */
  .lash-box{left:520px;top:589px;width:162px;height:427px}
  .lash-box .logo{top:60px;font-size:36px}
  .lash-box .copy{top:274px;font-size:13px}
  .lash-box .rule{width:58px}
  .lash-box .volume{bottom:24px;font-size:15px}
  .lash-label{left:719px;top:716px;width:58px;height:293px}
  .lash-label .logo{top:42px;font-size:18px}
  .lash-label .copy{top:191px;font-size:8.5px}
  .lash-label .rule{width:36px;height:1px}
  .lash-label .volume{bottom:12px;font-size:10px}

  /* Eyebrow */
  .brow-box{left:878px;top:590px;width:162px;height:423px}
  .brow-box .logo{top:60px;font-size:36px}
  .brow-box .copy{top:272px;font-size:13px}
  .brow-box .rule{width:58px}
  .brow-box .volume{bottom:24px;font-size:15px}
  .brow-label{left:1078px;top:716px;width:58px;height:293px}
  .brow-label .logo{top:42px;font-size:18px}
  .brow-label .copy{top:191px;font-size:8.5px}
  .brow-label .rule{width:36px;height:1px}
  .brow-label .volume{bottom:12px;font-size:10px}
</style>
</head>
<body>
<main class="canvas">

  <section class="face hair-box">
    <div class="flora flora--top" role="img" aria-label="Line-drawn floral sprig"></div>
    <div class="flora flora--bottom" role="img" aria-label="Line-drawn floral sprig"></div>
    <h1 class="logo logo--vertical">VelaMira</h1>
    <p class="copy">Hair<br>Growth<span class="rule"></span>Serum</p>
    <p class="volume">50ml</p>
  </section>

  <section class="face hair-wrap">
    <div class="flora flora--top" role="img" aria-label="Line-drawn floral sprig"></div>
    <div class="flora flora--bottom" role="img" aria-label="Line-drawn floral sprig"></div>
    <h2 class="logo logo--vertical">VelaMira</h2>
    <p class="copy">Hair<br>Growth<span class="rule"></span>Serum</p>
    <p class="volume">50ml</p>
  </section>

  <section class="face serum-box">
    <div class="flora flora--top" role="img" aria-label="Line-drawn floral garland"></div>
    <div class="flora flora--bottom" role="img" aria-label="Line-drawn floral garland"></div>
    <h2 class="logo logo--horizontal">VelaMira</h2>
    <p class="copy">Anti Aging<span class="rule"></span>Serum</p>
    <p class="volume">30ml</p>
  </section>

  <section class="face serum-label">
    <div class="flora flora--top" role="img" aria-label="Line-drawn floral sprig"></div>
    <div class="flora flora--bottom" role="img" aria-label="Line-drawn floral sprig"></div>
    <h2 class="logo logo--horizontal">VelaMira</h2>
    <p class="copy">Anti Aging<span class="rule"></span>Serum</p>
    <p class="volume">30ml</p>
  </section>

  <section class="face mascara-box">
    <div class="flora flora--top" role="img" aria-label="Line-drawn floral sprig"></div>
    <div class="flora flora--bottom" role="img" aria-label="Line-drawn floral sprig"></div>
    <h2 class="logo logo--vertical">VelaMira</h2>
    <p class="volume">5ml</p>
  </section>

  <section class="face mascara-label">
    <div class="flora flora--top" role="img" aria-label="Line-drawn floral sprig"></div>
    <h2 class="logo logo--vertical">VelaMira</h2>
    <p class="volume">5ml</p>
  </section>

  <section class="face lash-box">
    <div class="flora flora--top" role="img" aria-label="Line-drawn floral sprig"></div>
    <div class="flora flora--bottom" role="img" aria-label="Line-drawn floral sprig"></div>
    <h2 class="logo logo--vertical">VelaMira</h2>
    <p class="copy">Eyelash<br>Growth<span class="rule"></span>Serum</p>
    <p class="volume">5ml</p>
  </section>

  <section class="face lash-label">
    <div class="flora flora--top" role="img" aria-label="Line-drawn floral sprig"></div>
    <h2 class="logo logo--vertical">VelaMira</h2>
    <p class="copy">Eyelash<br>Growth<span class="rule"></span>Serum</p>
    <p class="volume">5ml</p>
  </section>

  <section class="face brow-box">
    <div class="flora flora--top" role="img" aria-label="Line-drawn floral sprig"></div>
    <div class="flora flora--bottom" role="img" aria-label="Line-drawn floral sprig"></div>
    <h2 class="logo logo--vertical">VelaMira</h2>
    <p class="copy">Eyebrow<br>Growth<span class="rule"></span>Serum</p>
    <p class="volume">5ml</p>
  </section>

  <section class="face brow-label">
    <div class="flora flora--top" role="img" aria-label="Line-drawn floral sprig"></div>
    <h2 class="logo logo--vertical">VelaMira</h2>
    <p class="copy">Eyebrow<br>Growth<span class="rule"></span>Serum</p>
    <p class="volume">5ml</p>
  </section>

</main>
</body>
</html>
```